verdant terraces simple classy business card design

my name is colin barrow and I run a gardening business aimed at high class verdant terraces. the business name is verdant terraces and our logo was designed on pixel harbour .My clientel are anything from residential homes to businesses. I take pride in my work and know that I offer a service like no other in my area.
The business card will be used to represent my business and I want it to be not only rememberable, but simplistic and modern. Eye catching too. Of course I would like it relatable to gardening and appealing to the correct clientel - those being garden enthusiasts, prestigious homes and businesses that are after top of the line gardening services like no other on the market.
I am not a typical lawn mowing business so I don't want a typical card design that represents that. The gardens I work with are generally million dollar properties with owners who are very garden proud looking for upkeep and guidance from me along with sometimes whole new garden designs. I want the business cards to show to my clients that I take pride, as they do, in their garden. And I want them to know from my card that I am a professional, qualified horticulturist offering them a top of the line service for life. I want them to refer my business on. I want them to look at my business card and see class and professionalism in a modern unique bold way.
The card should be simple with the possibility of the logo on the front being embossed/debossed and my details on the back the card should have a organic garden feel it's very important to me that it is absolutely perfect
I am also very open to ideas and suggestions so look forward to seeing the designs. the business logo has been supplied with this project and I want the card to be double sided

Contact info is
Colin Barrow - Managing Director / Horticulturist
Phone : 0481 526 704
Email: colinbarrow@verdantterraces.example.au

Target Market(s)

high class gardens residential and commercial

Industry/Entity Type

Gardener

Contact Information for Business Card

Contact info is
Phone : 0481 526 704

PLEASE MAKE CARD DOUBLE SIDED

Requirements
Must have
• organic simple classy modern feel
• must flow with the current logo that has been supplied with this project
• Double sided
• Must explain in a simple way that I deal with high end gardens and I'm a qualified horticulturist
Nice to have
• embossed debossed logo
Should not have
• shouldn't be to busy or cheap looking

```html
<!DOCTYPE html>
<html lang="en">
<head>
<meta charset="utf-8">
<title>Verdant Terraces – Business Card</title>
<link rel="stylesheet" href="https://fonts.googleapis.com/css2?family=Lora:wght@400;500&display=swap">
<style>
  :root {
    --bg: #e8ebeb;
    --card: #ffffff;
    --leaf: #62984f;
    --brand: #4e8a3c;
    --ink: #3a3a3a;
    --shadow: rgba(0, 0, 0, 0.12);
  }
  * { box-sizing: border-box; margin: 0; padding: 0; }
  html, body {
    width: 1200px; height: 900px; overflow: hidden;
    background: var(--bg);
    font-family: "Lora", Georgia, serif;
  }
  .canvas {
    width: 1200px; height: 900px;
    display: flex; flex-direction: column;
    align-items: center; justify-content: center; gap: 60px;
  }
  .card {
    position: relative;
    width: 580px; height: 354px;
    background: var(--card);
    box-shadow: 0 6px 18px var(--shadow);
    overflow: hidden;
  }
  .card__band {
    position: absolute; inset: 0;
    width: 100%; height: 100%;
  }
  .card__band polygon { fill: var(--leaf); }

  .brand {
    position: absolute;
    display: flex; align-items: center; gap: 14px;
    color: var(--brand);
    font-weight: 500;
  }
  .brand__dot {
    width: 46px; height: 46px; border-radius: 50%;
    background: var(--brand);
    flex: none;
  }
  .brand__name {
    display: flex; flex-direction: column; line-height: 1.05;
    text-transform: uppercase;
  }
  .brand__word--main { font-size: 30px; letter-spacing: 2px; }
  .brand__word--sub { font-size: 17px; letter-spacing: 12px; padding-left: 4px; }

  /* details side */
  .card--details .brand { left: 56px; top: 92px; }
  .contact {
    position: absolute; left: 56px; bottom: 46px;
    color: var(--ink);
  }
  .contact__name { font-size: 21px; font-weight: 400; }
  .contact__role { font-size: 14px; color: var(--brand); margin-bottom: 10px; }
  .contact__line { font-size: 14px; line-height: 1.45; }

  /* logo side */
  .card--logo .brand { right: 56px; top: 50%; transform: translateY(-50%); }
</style>
</head>
<body>
<main class="canvas">

  <section class="card card--details" aria-label="Business card, details side">
    <svg class="card__band" viewBox="0 0 100 100" preserveAspectRatio="none" aria-hidden="true">
      <polygon points="52,0 100,0 100,82"/>
    </svg>
    <div class="brand">
      <span class="brand__dot" aria-hidden="true"></span>
      <span class="brand__name">
        <span class="brand__word--main">Verdant</span>
        <span class="brand__word--sub">Terraces</span>
      </span>
    </div>
    <div class="contact">
      <p class="contact__name">Colin Barrow</p>
      <p class="contact__role">Managing Director</p>
      <p class="contact__line">0481 526 704</p>
      <p class="contact__line">colinbarrow@verdantterraces.example.au</p>
    </div>
  </section>

  <section class="card card--logo" aria-label="Business card, logo side">
    <svg class="card__band" viewBox="0 0 100 100" preserveAspectRatio="none" aria-hidden="true">
      <polygon points="0,0 26,0 58,100 0,100"/>
    </svg>
    <div class="brand">
      <span class="brand__dot" aria-hidden="true"></span>
      <span class="brand__name">
        <span class="brand__word--main">Verdant</span>
        <span class="brand__word--sub">Terraces</span>
      </span>
    </div>
  </section>

</main>
</body>
</html>
```